Web portal for events

The project is about creating a web application - portal for culture events in Denmark.

Design

We aim for very simplistic, light and fully responsive design. The white background is preferable, as well as light color tones. As inspirational points we like the colors used in www.parvolio.com and www.brindlemoor.org

FORMAT AND REQUIREMENTS:
1. Design should be provided based on the wireframes specified as a link below.
2. The design (and all of its pages) should be provided in three resolution variants:
- Desktop
- Tablet
- Phone
3. The design should be provided as PSD, where each page/section should be in its own PSD file
4. All graphical elements in the design should be delivered as single layers which can then be extracted from the PSD.
5. All graphical elements (icons, graphical buttons, etc.) should be provided as vector objects in the PSD, so that they can be exported into different sizes without loss of quality (for responsiveness)
6. The design should use either web safe fonts or Google Fonts.

RESPONSIVENESS
The web application should be visible on any devices (i.e. responsive design)

WIREFRAMES:
https://velkotrams.examplewire.com/projects/fennoplex/prototype/Homepage?key=3b7c19d0f2a84e6c5d1e9a07b4f2c8d6e1a3f590

We expect design of the following wireframes:

Homepage:
https://velkotrams.examplewire.com/projects/fennoplex/Homepage

For arrangører - billede uploaded:
https://velkotrams.examplewire.com/projects/fennoplex/For%20arrang%C3%B8rer%20-%20billede%20uploaded

Further specifications of the project (i.e. functionality, etc.):
https://files.quorvane.net/document/d/8pKw_Rt2mZqLx4NvB7yHc0aEs9uGdJf3TiOb6nVlW1k/edit?usp=sharing

```html
<!DOCTYPE html>
<html lang="da">
<head>
<meta charset="utf-8">
<title>Kultivo – Featured Events</title>
<link href="https://fonts.googleapis.com/css2?family=Questrial&display=swap" rel="stylesheet">
<style>
:root{
  --blue:#2a6fc4;
  --blue-dark:#1f5aa6;
  --navy-btn:#1d59a8;
  --navy-btn-edge:#123f7c;
  --orange:#ff8a12;
  --orange-edge:#d96a00;
  --heading:#1f5fa8;
  --nav:#3a3a3a;
  --text:#333;
  --muted:#666;
  --card-bg:#f7f7f7;
  --card-line:#dcdcdc;
  --footer:#3b3b3b;
}
*{box-sizing:border-box;margin:0;padding:0}
html,body{width:1086px;height:1200px;overflow:hidden;background:#fff}
body{font-family:"Questrial",sans-serif;color:var(--text);position:relative}
h2,h3{font-weight:normal}

.site-header{position:absolute;left:0;top:0;width:1086px;height:83px;background:var(--blue);border-bottom:2px solid var(--blue-dark)}
.brand{position:absolute;left:67px;top:24px;width:125px;font-size:25px;color:#fff;letter-spacing:0;line-height:1;white-space:nowrap}
.search{position:absolute;left:202px;top:24px;width:421px;height:27px;background:#fff;border-radius:14px}
.search svg{position:absolute;right:10px;top:5px}
.advanced{position:absolute;left:634px;top:31px;color:#fff;font-size:11.5px;letter-spacing:.5px}
.auth{position:absolute;left:878px;top:22px;width:141px;height:33px;background:var(--orange);border-bottom:3px solid var(--orange-edge);border-radius:2px;color:#fff;font-size:11.5px;text-align:center;line-height:31px;letter-spacing:.5px}

.category-nav{position:absolute;left:67px;top:98px;width:952px;height:39px;background:var(--nav);border-radius:20px;display:flex;justify-content:space-between;align-items:center;padding:0 29px;color:#fff;font-size:12.5px;letter-spacing:.3px}

.section-head{position:absolute;left:67px;top:168px;width:708px;height:24px}
.section-title{position:absolute;left:0;top:2px;color:var(--heading);font-size:18px;letter-spacing:.5px}
.section-rule{position:absolute;left:182px;top:12px;width:255px;height:1px;background:#bbb}
.sort-label{position:absolute;left:445px;top:5px;font-size:12px;color:#444;letter-spacing:.3px}
.sort-btn{position:absolute;top:2px;height:21px;background:#f2f2f2;border:1px solid #d6d6d6;font-size:10.5px;color:#777;font-style:italic;line-height:19px;text-align:center}
.sort-select{left:522px;width:82px;text-align:left;padding-left:8px}
.sort-select svg{position:absolute;right:6px;top:8px}
.sort-date{left:614px;width:43px}
.sort-price{left:667px;width:42px}

.event-grid{position:absolute;left:67px;top:208px;display:grid;grid-template-columns:repeat(3,219px);grid-auto-rows:257px;column-gap:26px;row-gap:22px}
.event-card{position:relative;background:var(--card-bg);border:1px solid var(--card-line)}
.event-photo{position:absolute;left:11px;top:13px;width:195px;height:114px}
.event-title{position:absolute;left:11px;top:138px;font-size:12px;color:#222;letter-spacing:.3px;white-space:nowrap}
.event-meta{position:absolute;left:11px;top:159px;width:185px;display:flex;justify-content:space-between;font-size:11px;color:var(--muted)}
.btn-events{position:absolute;left:11px;top:183px;width:79px;height:26px;background:var(--orange);border-bottom:3px solid var(--orange-edge);border-radius:2px;color:#fff;font-size:10px;text-align:center;line-height:24px;letter-spacing:.6px}
.btn-fav{position:absolute;left:11px;top:218px;width:182px;height:26px;background:var(--navy-btn);border-bottom:3px solid var(--navy-btn-edge);border-radius:2px;color:#fff;font-size:10px;text-align:center;line-height:24px;letter-spacing:.6px;white-space:nowrap}

.side-box{position:absolute;left:801px;width:218px;background:var(--card-bg);border:1px solid var(--card-line);text-align:center}
.side-title{color:var(--heading);font-size:18px;letter-spacing:.5px}
.favorites{top:170px;height:410px}
.favorites .side-title{margin-top:15px}
.fav-tile{position:absolute;left:13px;width:191px;height:91px}
.fav-caption{position:absolute;left:0;bottom:0;width:100%;height:26px;background:rgba(20,20,20,.85);color:#fff;font-size:11px;line-height:26px}
.btn-see{position:absolute;left:35px;top:363px;width:147px;height:33px;background:var(--orange);border-bottom:3px solid var(--orange-edge);border-radius:2px;color:#fff;font-size:11px;line-height:31px;letter-spacing:.5px}

.newsletter{top:598px;height:204px}
.newsletter .side-title{margin-top:18px}
.newsletter p{margin:10px 14px 0;font-size:11px;line-height:15px;color:#333}
.email-field{position:absolute;left:15px;top:123px;width:188px;height:31px;background:#fff;border:1px solid #d4d4d4;font-size:11px;color:#999;line-height:29px}
.btn-join{position:absolute;left:65px;top:163px;width:89px;height:31px;background:var(--orange);border-bottom:3px solid var(--orange-edge);border-radius:2px;color:#fff;font-size:11px;line-height:29px;letter-spacing:.5px}

.connect{top:820px;height:92px}
.connect .side-title{margin-top:18px}
.social{position:absolute;left:12px;top:51px;display:flex;gap:7px}
.social span{width:26px;height:26px;display:block}

.pager{position:absolute;left:299px;top:1068px;width:244px;height:33px;background:#f4f4f4;border:1px solid #d4d4d4;font-size:11px;color:#444;text-align:center;line-height:31px;letter-spacing:.3px}
.pager .current{color:var(--heading)}

.site-footer{position:absolute;left:0;top:1125px;width:1086px;height:75px;background:var(--footer);color:#ddd;text-align:center}
.footer-links{margin-top:21px;font-size:11.5px;white-space:nowrap}
.footer-links span{margin:0 7px}
.copyright{margin-top:7px;font-size:11px;color:#bbb}
</style>
</head>
<body>

<header class="site-header">
  <div class="brand">KULTIVO</div>
  <div class="search">
    <svg width="18" height="16" viewBox="0 0 18 16"><circle cx="7" cy="7" r="5" fill="none" stroke="#ff8a12" stroke-width="2.2"/><line x1="10.5" y1="10" x2="16" y2="14" stroke="#ff8a12" stroke-width="3" stroke-linecap="round"/></svg>
  </div>
  <div class="advanced">ADVANCED SEARCH</div>
  <div class="auth">LOG IN &nbsp;|&nbsp; SIGN UP</div>
</header>

<nav class="category-nav">
  <span>ALLE</span><span>MUSIK</span><span>SPORT</span><span>TEATER</span><span>UDSTILLING</span><span>AELDRE</span><span>BORN</span><span>MOTION</span><span>DIVERSE</span>
</nav>

<div class="section-head">
  <h2 class="section-title">FEATURED EVENTS</h2>
  <div class="section-rule"></div>
  <span class="sort-label">Sorter &nbsp;efter</span>
  <span class="sort-btn sort-select">Polulaere<svg width="8" height="5" viewBox="0 0 8 5"><path d="M0 0h8L4 5z" fill="#888"/></svg></span>
  <span class="sort-btn sort-date">Dato</span>
  <span class="sort-btn sort-price">Pris</span>
</div>

<main class="event-grid">
  <article class="event-card">
    <div class="event-photo" role="img" aria-label="Cyclists racing in a pack on a tree-lined road" style="background:linear-gradient(135deg,#4d6a3a,#a8a29a 55%,#3b3f4a)"></div>
    <h3 class="event-title">JONAS VENDEL KONCERT</h3>
    <div class="event-meta"><span>Oplev xxxx.....</span><span>20/2/2014</span></div>
    <div class="btn-events">SE EVENTS</div>
    <div class="btn-fav">TILLFOJ TIL MINE FAVORITTER</div>
  </article>
  <article class="event-card">
    <div class="event-photo" role="img" aria-label="Crowd at a busy street food stall under a red sign" style="background:linear-gradient(160deg,#2a2020,#8a2a22 40%,#5a4a42)"></div>
    <h3 class="event-title">JONAS VENDEL KONCERT</h3>
    <div class="event-meta"><span>Oplev xxxx.....</span><span>20/2/2014</span></div>
    <div class="btn-events">SE EVENTS</div>
    <div class="btn-fav">TILLFOJ TIL MINE FAVORITTER</div>
  </article>
  <article class="event-card">
    <div class="event-photo" role="img" aria-label="Costumed street performers in red and white at a festive parade" style="background:linear-gradient(120deg,#8a1e1e,#d9d4cc 55%,#5a4b3e)"></div>
    <h3 class="event-title">JONAS VENDEL KONCERT</h3>
    <div class="event-meta"><span>Oplev xxxx.....</span><span>20/2/2014</span></div>
    <div class="btn-events">SE EVENTS</div>
    <div class="btn-fav">TILLFOJ TIL MINE FAVORITTER</div>
  </article>

  <article class="event-card">
    <div class="event-photo" role="img" aria-label="Colourful music-themed artwork in purple and pink tones" style="background:linear-gradient(120deg,#b84cae,#9a3fc0 50%,#e7b2e4)"></div>
    <h3 class="event-title">JONAS VENDEL KONCERT</h3>
    <div class="event-meta"><span>Oplev xxxx.....</span><span>20/2/2014</span></div>
    <div class="btn-events">SE EVENTS</div>
    <div class="btn-fav">TILLFOJ TIL MINE FAVORITTER</div>
  </article>
  <article class="event-card">
    <div class="event-photo" role="img" aria-label="Football team in white kits celebrating in a stadium" style="background:linear-gradient(180deg,#3a3a3a,#cfcfcf 55%,#2e4a2a)"></div>
    <h3 class="event-title">JONAS VENDEL KONCERT</h3>
    <div class="event-meta"><span>Oplev xxxx.....</span><span>20/2/2014</span></div>
    <div class="btn-events">SE EVENTS</div>
    <div class="btn-fav">TILLFOJ TIL MINE FAVORITTER</div>
  </article>
  <article class="event-card">
    <div class="event-photo" role="img" aria-label="Horse-drawn royal carriage in front of a palace facade" style="background:linear-gradient(180deg,#b8a48a,#8c7d6c 55%,#6b6e70)"></div>
    <h3 class="event-title">JONAS VENDEL KONCERT</h3>
    <div class="event-meta"><span>Oplev xxxx.....</span><span>20/2/2014</span></div>
    <div class="btn-events">SE EVENTS</div>
    <div class="btn-fav">TILLFOJ TIL MINE FAVORITTER</div>
  </article>

  <article class="event-card">
    <div class="event-photo" role="img" aria-label="Large crowd at an outdoor city street festival" style="background:linear-gradient(170deg,#b9a79a,#6b4a3c 50%,#3a3a34)"></div>
    <h3 class="event-title">JONAS VENDEL KONCERT</h3>
    <div class="event-meta"><span>Oplev xxxx.....</span><span>20/2/2014</span></div>
    <div class="btn-events">SE EVENTS</div>
    <div class="btn-fav">TILLFOJ TIL MINE FAVORITTER</div>
  </article>
  <article class="event-card">
    <div class="event-photo" role="img" aria-label="Dancers under yellow banners at an outdoor festival" style="background:linear-gradient(120deg,#3d5a6a,#e6c22a 50%,#6b7a3a)"></div>
    <h3 class="event-title">JONAS VENDEL KONCERT</h3>
    <div class="event-meta"><span>Oplev xxxx.....</span><span>20/2/2014</span></div>
    <div class="btn-events">SE EVENTS</div>
    <div class="btn-fav">TILLFOJ TIL MINE FAVORITTER</div>
  </article>
  <article class="event-card">
    <div class="event-photo" role="img" aria-label="Carnival dancers in bright feathered costumes" style="background:linear-gradient(120deg,#8a5a3a,#d9b84a 45%,#4aa0b0)"></div>
    <h3 class="event-title">JONAS VENDEL KONCERT</h3>
    <div class="event-meta"><span>Oplev xxxx.....</span><span>20/2/2014</span></div>
    <div class="btn-events">SE EVENTS</div>
    <div class="btn-fav">TILLFOJ TIL MINE FAVORITTER</div>
  </article>
</main>

<aside>
  <section class="side-box favorites">
    <h2 class="side-title">MINE FAVORITTER</h2>
    <div class="fav-tile" style="top:48px;background:linear-gradient(135deg,#3a4a7a,#b03a4a 55%,#2a2a2a)" role="img" aria-label="Crowd of fans at a sports event">
      <div class="fav-caption">Text goes here</div>
    </div>
    <div class="fav-tile" style="top:151px;background:linear-gradient(135deg,#4a6a3a,#4a8ac0 55%,#2a2a2a)" role="img" aria-label="Runners in a park race">
      <div class="fav-caption">Text goes here</div>
    </div>
    <div class="fav-tile" style="top:253px;background:linear-gradient(135deg,#6a8a4a,#3a5aa0 50%,#b04a4a)" role="img" aria-label="Mass start of a city marathon">
      <div class="fav-caption">Text goes here</div>
    </div>
    <div class="btn-see">SEE MINE FAVORITTER</div>
  </section>

  <section class="side-box newsletter">
    <h2 class="side-title">NYHEDSBREV</h2>
    <p>Lorem ipsum dolor sit amet, consectetur adipisicing eitseo eiusmod tempor incididunt ut labore et dolore magna aliqua.</p>
    <div class="email-field">Enter Email Address</div>
    <div class="btn-join">TILMED</div>
  </section>

  <section class="side-box connect">
    <h2 class="side-title">CONNECT US</h2>
    <div class="social">
      <span style="background:#27a9e1" aria-label="Social profile 1"></span>
      <span style="background:#3b5998" aria-label="Social profile 2"></span>
      <span style="background:#c8232c" aria-label="Social profile 3"></span>
      <span style="background:#3a3a3a" aria-label="Social profile 4"></span>
      <span style="background:#f7931e" aria-label="Feed"></span>
      <span style="background:#d0232a" aria-label="Video channel"></span>
    </div>
  </section>
</aside>

<div class="pager">&lsaquo;&lsaquo; PREV &nbsp;&nbsp;| &nbsp;<span class="current">1</span>&nbsp; | &nbsp;2&nbsp; | &nbsp;3&nbsp; | &nbsp;4&nbsp; | &nbsp;LAST &nbsp;&rsaquo;&rsaquo;</div>

<footer class="site-footer">
  <div class="footer-links">Om Kultivo<span>|</span>Vilkar betingelser<span>|</span>Kopspolitik<span>|</span>Nyhedsbrev<span>|</span>kontackt<span>|</span>Log In / Register<span>|</span>help<span>|</span>For Arrangorer<span>|</span>For Kommuner og turistforninger</div>
  <div class="copyright">Copyright © 2014. All Right Reserved</div>
</footer>

</body>
</html>
```